Every Shelf Set Neatly or ESN Organized needs a business card design. ESN Organized is a professi

We need a business card design that is clean, sharp and conveys a sense of organization. I already have a logo.

Target Market(s)

Families (specifically mothers), small business owners, parents, seniors

Industry/Entity Type

Business

Contact Information for Business Card

My website is www.esnorganized-example.com and my Facebook page is http://www.sociallink-example.com/everyshelfsetneatly. The phone number is 418-552-7094 and I want to be listed as Lorna M. Pelham, Owner

Requirements
Must have
• My logo.

```html
<!DOCTYPE html>
<html lang="en">
<head>
<meta charset="utf-8">
<title>Every Shelf Set Neatly – Business Card</title>
<link rel="stylesheet" href="https://fonts.googleapis.com/css2?family=Arimo:wght@400&display=swap">
<style>
  :root {
    --page-bg: #e6e4e0;
    --card-black: #070707;
    --card-sheen: #2a2a2a;
    --accent-blue: #2f7fc1;
    --text-white: #f2f2f2;
    --text-grey: #d9d9d9;
  }
  html, body {
    margin: 0;
    width: 1200px;
    height: 1022px;
    overflow: hidden;
    background: var(--page-bg);
  }
  .card {
    position: absolute;
    left: 180px;
    top: 271px;
    width: 840px;
    height: 480px;
    border-radius: 18px;
    overflow: hidden;
    background:
      linear-gradient(115deg, var(--card-black) 0%, var(--card-sheen) 38%, var(--card-black) 62%, var(--card-black) 100%);
    box-shadow: 0 20px 50px rgba(0,0,0,0.35);
    font-family: "Arimo", Arial, sans-serif;
  }
  .bottom-band {
    position: absolute;
    left: 0;
    bottom: 0;
    width: 520px;
    height: 16px;
    background: var(--accent-blue);
  }
  .brand {
    position: absolute;
    left: 64px;
    top: 100px;
    display: flex;
    align-items: center;
    gap: 14px;
  }
  .brand-dot {
    width: 14px;
    height: 14px;
    border-radius: 50%;
    background: var(--text-white);
  }
  .brand-name {
    font-weight: 400;
    font-size: 34px;
    color: var(--text-white);
  }
  .divider-line {
    position: absolute;
    left: 300px;
    top: 258px;
    width: 500px;
    height: 2px;
    background: var(--accent-blue);
  }
  .divider-stem {
    position: absolute;
    left: 300px;
    top: 258px;
    width: 2px;
    height: 150px;
    background: var(--accent-blue);
  }
  .holder-name {
    position: absolute;
    right: 44px;
    top: 216px;
    font-size: 34px;
    color: var(--accent-blue);
  }
  .holder-role {
    position: absolute;
    right: 40px;
    top: 268px;
    font-size: 18px;
    color: var(--text-grey);
  }
  .contacts {
    position: absolute;
    left: 318px;
    top: 318px;
    margin: 0;
    padding: 0;
    list-style: none;
  }
  .contacts li {
    display: flex;
    align-items: center;
    gap: 10px;
    height: 28px;
    font-size: 19px;
    color: var(--text-white);
  }
  .contacts svg {
    width: 14px;
    height: 14px;
    flex: none;
  }
</style>
</head>
<body>
  <div class="card">
    <div class="brand">
      <span class="brand-dot"></span>
      <span class="brand-name">Every Shelf Set Neatly</span>
    </div>

    <div class="divider-line"></div>
    <div class="divider-stem"></div>

    <div class="holder-name">Lorna M. Pelham</div>
    <div class="holder-role">Owner</div>

    <ul class="contacts">
      <li>
        <svg viewBox="0 0 16 16" aria-hidden="true">
          <path d="M4 1.5 L6.2 4.6 5 6.2 C5.8 8 7.8 10 9.8 11 L11.4 9.8 14.5 12 13 14.5 C7.5 14 2 8.5 1.5 3 Z" fill="var(--accent-blue)"/>
        </svg>
        418-552-7094
      </li>
      <li>
        <svg viewBox="0 0 16 16" aria-hidden="true">
          <g fill="none" stroke="var(--accent-blue)" stroke-width="1.4">
            <circle cx="8" cy="8" r="6.5"/>
            <ellipse cx="8" cy="8" rx="3" ry="6.5"/>
            <line x1="1.5" y1="8" x2="14.5" y2="8"/>
          </g>
        </svg>
        www.esnorganized-example.com
      </li>
      <li>
        <svg viewBox="0 0 16 16" aria-hidden="true">
          <circle cx="8" cy="8" r="6" fill="var(--accent-blue)"/>
        </svg>
        www.sociallink-example.com/everyshelfsetneatly
      </li>
    </ul>

    <div class="bottom-band"></div>
  </div>
</body>
</html>
```